Become a Mentor - For Musicians, Artists, Producers and Teachers

Here is the full creative brief:

https://files.quorvant.com/sheets/d/7kTbWmQa2_pLRz9XcN4eHs8JuYd3FoVgA6iBnCqE/view?mode=shared

Here is the background image file: https://www.stashvel.com/sh/48kdmwtnb7yrs2p/AAZm3kLPQwTx8VnHRe4jBcDu?dl=0

LOGO:
https://www.stashvel.com/sh/k382fubotn7wq6/AAJhT5LsRy2D-mKzPX9CvGhNb?dl=0

```html
<!DOCTYPE html>
<html lang="en">
<head>
<meta charset="utf-8">
<title>Become a Mentor – Meridian School of Music</title>
<link rel="stylesheet" href="https://fonts.googleapis.com/css2?family=Encode+Sans+Condensed:wght@500;600;700&family=Montserrat:wght@800;900&family=Signika:wght@600;700&display=swap">
<style>
  :root {
    --photo-dark: #1c1d20;
    --photo-mid: #3a3b3f;
    --photo-warm: #4a3a33;
    --brand-orange: #ff7f00;
    --panel-left: #dc6609;
    --panel-right: #ff8206;
    --white: #ffffff;
    --shadow: rgba(0, 0, 0, 0.35);
  }
  * { margin: 0; padding: 0; box-sizing: border-box; }
  html, body { width: 848px; height: 1200px; overflow: hidden; background: var(--white); }
  .poster {
    position: relative;
    width: 848px;
    height: 1200px;
    overflow: hidden;
    font-family: "Encode Sans Condensed", "Arial Narrow", sans-serif;
    color: var(--white);
  }

  /* Hero photo area */
  .hero-photo {
    position: absolute;
    left: 0; top: 0;
    width: 848px; height: 640px;
    background:
      radial-gradient(ellipse 260px 320px at 560px 360px, var(--photo-warm) 0%, transparent 70%),
      radial-gradient(ellipse 300px 260px at 260px 260px, var(--photo-mid) 0%, transparent 75%),
      linear-gradient(180deg, #2c2d31 0%, var(--photo-dark) 100%);
  }

  /* Brand lockup */
  .brand {
    position: absolute;
    right: 12px; top: 48px;
    width: 210px;
    text-align: center;
  }
  .brand__mark {
    display: inline-block;
    width: 12px; height: 12px;
    border-radius: 50%;
    background: var(--white);
    margin-bottom: 6px;
  }
  .brand__name {
    font-family: "Montserrat", sans-serif;
    font-weight: 800;
    font-size: 18px;
    line-height: 1.1;
    letter-spacing: 0.5px;
    color: var(--white);
  }
  .brand__tagline {
    font-family: "Encode Sans Condensed", sans-serif;
    font-weight: 500;
    font-size: 8.5px;
    margin-top: 3px;
    color: var(--white);
  }

  /* Headline block */
  .headline {
    position: absolute;
    left: 119px; top: 290px;
    width: 341px;
    text-align: center;
  }
  .headline__kicker {
    font-family: "Signika", sans-serif;
    font-weight: 600;
    font-size: 13.5px;
    letter-spacing: 2.6px;
    line-height: 20px;
  }
  .headline__rule {
    height: 3px;
    background: var(--white);
  }
  .headline__title {
    font-family: "Signika", sans-serif;
    font-weight: 700;
    font-size: 46px;
    line-height: 54px;
    color: var(--brand-orange);
    letter-spacing: -0.6px;
    white-space: nowrap;
  }
  .headline__sub {
    font-family: "Signika", sans-serif;
    font-weight: 600;
    font-size: 13.5px;
    letter-spacing: 3.4px;
    line-height: 20px;
    margin-top: 7px;
  }

  /* Goals list */
  .goals {
    list-style: none;
  }
  .goals__item {
    position: absolute;
    left: 111px;
    font-size: 16.5px;
    font-weight: 600;
    line-height: 25px;
    white-space: nowrap;
  }
  .goals__item--first { top: 471px; }
  .goals__item--second { top: 527px; }
  .goals__tick {
    position: absolute;
    left: -40px; top: 3px;
    width: 26px; height: 19px;
  }

  /* Lower panels */
  .panel {
    position: absolute;
    top: 640px;
    height: 560px;
  }
  .panel--purpose { left: 0; width: 419px; background: var(--panel-left); }
  .panel--opportunity { left: 419px; width: 429px; background: var(--panel-right); }

  .panel__title {
    position: absolute;
    font-family: "Montserrat", sans-serif;
    font-weight: 900;
    font-size: 40px;
    line-height: 48px;
    letter-spacing: 0.5px;
    text-align: center;
  }
  .panel__rule {
    position: absolute;
    height: 6px;
    background: var(--white);
  }
  .panel__text {
    position: absolute;
    text-align: center;
    font-weight: 700;
    font-size: 27px;
    line-height: 47px;
    letter-spacing: -0.2px;
  }

  .panel--purpose .panel__title { left: 0; width: 402px; top: 68px; }
  .panel--purpose .panel__rule--top { left: 111px; width: 183px; top: 128px; }
  .panel--purpose .panel__text { left: 10px; width: 413px; top: 165px; }
  .panel--purpose .panel__rule--bottom { left: 34px; width: 360px; top: 339px; height: 7px; }

  .panel--opportunity .panel__title { left: 0; width: 410px; top: 67px; }
  .panel--opportunity .panel__rule--top { left: 92px; width: 234px; top: 128px; }
  .panel--opportunity .panel__text { left: 0; width: 424px; top: 144px; line-height: 48px; }
  .panel--opportunity .panel__rule--bottom { left: 44px; width: 360px; top: 444px; height: 7px; }

  .apply-button {
    position: absolute;
    left: 614px; top: 1121px;
    width: 200px; height: 40px;
    background: var(--white);
    transform: rotate(0.4deg);
    box-shadow: 6px 8px 10px var(--shadow);
    display: flex;
    align-items: center;
    justify-content: center;
    font-family: "Montserrat", sans-serif;
    font-weight: 900;
    font-size: 22px;
    letter-spacing: 0.5px;
    color: var(--brand-orange);
    text-shadow: 2px 2px 2px var(--shadow);
  }
</style>
</head>
<body>
<main class="poster">

  <div class="hero-photo" role="img" aria-label="Dimly lit recording studio with two musicians talking beside a mixing desk and studio speakers"></div>

  <div class="brand">
    <span class="brand__mark"></span>
    <div class="brand__name">MERIDIAN SCHOOL OF MUSIC</div>
    <div class="brand__tagline">...shaping a future of rhythm &amp; bold ideas.</div>
  </div>

  <header class="headline">
    <p class="headline__kicker">Start Your Career today</p>
    <div class="headline__rule"></div>
    <h1 class="headline__title">Become a Mentor</h1>
    <div class="headline__rule"></div>
    <p class="headline__sub">Mentor Career Development</p>
  </header>

  <ul class="goals">
    <li class="goals__item goals__item--first">
      <svg class="goals__tick" viewBox="0 0 28 22" aria-hidden="true"><path d="M1 12 L10 20 L27 2 L10 14 Z" fill="#ffffff"/></svg>
      To educate and transform the perception of our target market avatar<br>
      It's now possible to have a pro career as a mentor
    </li>
    <li class="goals__item goals__item--second">
      <svg class="goals__tick" viewBox="0 0 28 22" aria-hidden="true"><path d="M1 12 L10 20 L27 2 L10 14 Z" fill="#ffffff"/></svg>
      To be top of mind and maintain leadership position in the music indutsry for mentoring<br>
      career development for musicians, artists, producers and teachers in Australia
    </li>
  </ul>

  <section class="panel panel--purpose">
    <h2 class="panel__title">Purpose</h2>
    <div class="panel__rule panel__rule--top"></div>
    <p class="panel__text">To produce professional careers for<br>musicians, artists, producers<br>and teachers</p>
    <div class="panel__rule panel__rule--bottom"></div>
  </section>

  <section class="panel panel--opportunity">
    <h2 class="panel__title">Opportunity</h2>
    <div class="panel__rule panel__rule--top"></div>
    <p class="panel__text">Start Your Career<br>Become a Mentor Today<br>Turn your skills and passion<br>for music into a career<br>Designed for Musicians,<br>Artists, Producers &amp; Teachers</p>
    <div class="panel__rule panel__rule--bottom"></div>
  </section>

  <div class="apply-button">APPLY NOW</div>

</main>
</body>
</html>
```